Business card alterations

I have changed my business name from Brisa Laser Renewal Clinic to simply "Brisa Laser Clinic' and need this logo changed to reflect same

Brisa Laser Clinic
Est. 2004

I also need new business cards with above logo included and this attached card changed to the following.
Marianne Holcroft
Dermal Aesthetician
Grad Cert in Laser & IPL Treatments

I need at least one logo in less than 4mb so I can upload into my newsletter format so I can upload to newsletters, emails etc

Thanks
Mari

```html
<!DOCTYPE html>
<html lang="en">
<head>
<meta charset="utf-8">
<title>Brisa Laser Clinic — Business Card</title>
<link rel="stylesheet" href="https://fonts.googleapis.com/css2?family=Source+Sans+3:wght@400;600&display=swap">
<style>
  :root {
    --backdrop: #3b1614;
    --card-green: #0da158;
    --ink-white: #ffffff;
    --shadow: rgba(0, 0, 0, 0.45);
  }
  * { box-sizing: border-box; margin: 0; padding: 0; }
  html, body {
    width: 1200px;
    height: 800px;
    overflow: hidden;
    background: var(--backdrop);
  }
  .canvas {
    position: relative;
    width: 1200px;
    height: 800px;
    display: flex;
    align-items: center;
    justify-content: center;
  }
  .business-card {
    width: 820px;
    height: 500px;
    background: var(--card-green);
    color: var(--ink-white);
    font-family: "Source Sans 3", "Helvetica Neue", Arial, sans-serif;
    box-shadow: 0 18px 40px var(--shadow);
    display: flex;
    flex-direction: column;
    align-items: center;
    padding-top: 70px;
  }
  .brand {
    text-align: center;
  }
  .brand-name {
    font-size: 128px;
    font-weight: 400;
    line-height: 1;
    letter-spacing: 2px;
  }
  .brand-line {
    margin-top: 14px;
    font-size: 21px;
    font-weight: 400;
    letter-spacing: 11px;
    text-transform: uppercase;
  }
  .brand-est {
    margin-top: 4px;
    font-size: 21px;
    font-weight: 400;
    letter-spacing: 9px;
  }
  .details {
    margin-top: 44px;
    display: flex;
    align-items: stretch;
  }
  .person {
    text-align: right;
    padding-right: 22px;
    padding-top: 8px;
  }
  .person-name {
    font-size: 31px;
    font-weight: 600;
    line-height: 1.1;
  }
  .person-role {
    font-size: 19px;
    font-weight: 400;
    line-height: 1.3;
  }
  .divider {
    width: 2px;
    background: var(--ink-white);
  }
  .contact {
    list-style: none;
    padding-left: 22px;
    font-size: 19px;
    font-weight: 400;
    line-height: 1.3;
  }
  .contact-phone {
    font-weight: 600;
  }
</style>
</head>
<body>
  <main class="canvas">
    <section class="business-card" aria-label="Brisa Laser Clinic business card">
      <header class="brand">
        <div class="brand-name">Brisa</div>
        <div class="brand-line">Brisa Laser Clinic</div>
        <div class="brand-est">EST. 2004</div>
      </header>
      <div class="details">
        <div class="person">
          <div class="person-name">Marianne Holcroft</div>
          <div class="person-role">Dermal Aesthetician</div>
          <div class="person-role">Grad Cert in Laser &amp; IPL Treatments</div>
        </div>
        <div class="divider" aria-hidden="true"></div>
        <ul class="contact">
          <li class="contact-phone">T (08) 7421 3095</li>
          <li>info@brisaclinic.com.au</li>
          <li>www.brisaclinic.com.au</li>
          <li>148 Marlowe Road</li>
          <li>Hallett Park SA 5099</li>
        </ul>
      </div>
    </section>
  </main>
</body>
</html>
```